Half page (a5) ad for a company

I need a design for an ad for a company to be published in a conference catalogue. Please find enclosed the logo for a company. The company is providing health screening services. Ad should be subtle and minimalistic, i.e. logo in the centre and a phrase saying: "Be in charge of your own health" and the website bluefen.co.uk. Also please find enclosed guidlines for colours and fonts to be used.

```html
<!DOCTYPE html>
<html lang="en">
<head>
<meta charset="utf-8">
<title>Bluefen Private – A5 Ad</title>
<link href="https://fonts.googleapis.com/css2?family=Montserrat:wght@400;500;600&display=swap" rel="stylesheet">
<style>
  :root {
    --brand-red: #e30613;
    --brand-red-deep: #a50d1c;
    --ink: #0a0a0a;
    --paper: #ffffff;
    --backdrop: #e0e0e0;
  }
  * { margin: 0; padding: 0; box-sizing: border-box; }
  html, body {
    width: 1200px;
    height: 1200px;
    overflow: hidden;
    background: var(--backdrop);
    font-family: "Montserrat", sans-serif;
  }
  .ad {
    position: absolute;
    left: 212px;
    top: 50px;
    width: 777px;
    height: 1100px;
    background: var(--paper);
  }
  .brand {
    position: absolute;
    top: 140px;
    left: 0;
    right: 0;
    display: flex;
    flex-direction: column;
    align-items: center;
  }
  .brand-dot {
    width: 150px;
    height: 150px;
    border-radius: 50%;
    background: var(--brand-red);
  }
  .brand-name {
    margin-top: 62px;
    font-size: 66px;
    font-weight: 400;
    color: var(--brand-red);
    letter-spacing: 0.5px;
    line-height: 1;
  }
  .headline {
    position: absolute;
    top: 660px;
    left: 0;
    right: 0;
    text-align: center;
    font-size: 75px;
    font-weight: 600;
    line-height: 88px;
    letter-spacing: 0.5px;
  }
  .headline-lead { display: block; color: var(--ink); }
  .headline-accent { display: block; color: var(--brand-red); }
  .web-pill {
    position: absolute;
    top: 944px;
    left: 50%;
    transform: translateX(-50%);
    width: 259px;
    height: 56px;
    border-radius: 28px;
    background: linear-gradient(180deg, var(--brand-red) 0%, var(--brand-red) 55%, var(--brand-red-deep) 100%);
    color: var(--paper);
    font-size: 26px;
    font-weight: 500;
    display: flex;
    align-items: center;
    justify-content: center;
    letter-spacing: 0.3px;
  }
</style>
</head>
<body>
  <main class="ad">
    <div class="brand">
      <span class="brand-dot"></span>
      <span class="brand-name">Bluefen Private</span>
    </div>
    <h1 class="headline">
      <span class="headline-lead">Be in charge of</span>
      <span class="headline-accent">your own health</span>
    </h1>
    <div class="web-pill">bluefen.co.uk</div>
  </main>
</body>
</html>
```